Varnex Consulting Business card design.

See our website www.varnexconsulting.example which will give you a good idea of what we are about. The font is called 'Play'.

I'd like a standout business card in keeping with the themes and branding on the website

Target Market(s)

professionals. HR directors

Industry/Entity Type

Business

Contact Information for Business Card

Varnex Consulting PO Box 3172 Merrowdale NSW 2291 1300 485 193 Gavin Threlkeld Principal email: career@varnexconsulting.example ABN: 71203948865

Font styles to use
Other font styles liked:
• Play

Requirements
Must have
• Must have same design colours and branding as website.
• On back I'd prefer a list of the things we do which appears below the name at the header on the website

```html
<!DOCTYPE html>
<html lang="en">
<head>
<meta charset="utf-8">
<title>Varnex Consulting – Business Card</title>
<link rel="stylesheet" href="https://fonts.googleapis.com/css2?family=Play:wght@400;700&display=swap">
<style>
  :root {
    --navy: #0b2236;
    --navy-deep: #071a2a;
    --brand-blue: #1e88d8;
    --paper: #eeeff1;
    --ink: #1b1d22;
    --white: #ffffff;
    --backdrop: #d9d6d0;
    --sky-top: #0f4fae;
    --sky-mid: #2a7fe0;
    --snow: #dfe9f6;
  }
  * { margin: 0; padding: 0; box-sizing: border-box; }
  html, body {
    width: 1200px; height: 892px; overflow: hidden;
    background: var(--backdrop);
    font-family: "Play", sans-serif;
  }
  .sheet {
    width: 1200px; height: 892px;
    display: flex; flex-direction: column;
    align-items: center; justify-content: center; gap: 40px;
  }
  .card {
    width: 620px; height: 379px; display: block;
    box-shadow: 0 6px 18px rgba(0,0,0,.25);
  }
  .card-surface { fill: var(--paper); }
  .header-band { fill: var(--navy); }
  .brand-name { font-size: 38px; letter-spacing: 1px; }
  .brand-first { fill: var(--white); }
  .brand-second { fill: var(--brand-blue); }
  .services { fill: var(--brand-blue); font-size: 13px; letter-spacing: .8px; }
  .abn { fill: var(--brand-blue); font-size: 16px; font-weight: 700; }
  .person-name { fill: var(--brand-blue); font-size: 26px; }
  .person-role { fill: var(--ink); font-size: 18px; }
  .contact-line { fill: var(--ink); font-size: 15px; }
  .icon-tile { fill: var(--brand-blue); }
  .icon-glyph { fill: var(--white); }
  .icon-stroke { fill: none; stroke: var(--white); stroke-width: 1.2; }
  .back-surface { fill: var(--navy-deep); }
  .photo-frame { stroke: var(--white); stroke-width: 3; }
  .back-brand { fill: var(--navy); font-size: 40px; font-weight: 700; letter-spacing: 1px; }
  .back-services { fill: var(--white); font-size: 14px; letter-spacing: 1px; }
</style>
</head>
<body>
<main class="sheet">

  <svg class="card card-front" viewBox="0 0 620 379" aria-label="Business card front">
    <rect class="card-surface" width="620" height="379"/>
    <path class="header-band" d="M0 0 H600 C540 170 300 270 0 220 Z"/>
    <text class="brand-name" x="36" y="130"><tspan class="brand-first">VARNEX </tspan><tspan class="brand-second">CONSULTING</tspan></text>
    <text class="services" x="38" y="160">Search &amp; Select | Career | Coaching | Leadership | Outplacement</text>
    <text class="abn" x="596" y="212" text-anchor="end">ABN: 71203948865</text>

    <text class="person-name" x="40" y="256">Gavin Threlkeld</text>
    <text class="person-role" x="40" y="280">Principal</text>

    <g class="contact contact-phone">
      <rect class="icon-tile" x="40" y="294" width="14" height="14" rx="2"/>
      <path class="icon-glyph" d="M43.5 297 l2.5 0 1 3 -1.5 1 a6 6 0 0 0 3 3 l1 -1.5 3 1 0 2.5 a1 1 0 0 1 -1 1 a9 9 0 0 1 -9 -9 a1 1 0 0 1 1 -1 z"/>
      <text class="contact-line" x="64" y="306">1300 485 193</text>
    </g>
    <g class="contact contact-email">
      <rect class="icon-tile" x="40" y="318" width="14" height="14" rx="2"/>
      <rect class="icon-stroke" x="43" y="321.5" width="8" height="7"/>
      <path class="icon-stroke" d="M43 321.5 l4 3.5 4 -3.5"/>
      <text class="contact-line" x="64" y="330">career@varnexconsulting.example</text>
    </g>
    <g class="contact contact-address">
      <rect class="icon-tile" x="40" y="342" width="14" height="14" rx="2"/>
      <path class="icon-glyph" d="M47 353.5 l-3 -4.5 a3.4 3.4 0 1 1 6 0 z"/>
      <text class="contact-line" x="64" y="354">PO Box 3172 Merrowdale NSW 2291</text>
    </g>
  </svg>

  <svg class="card card-back" viewBox="0 0 620 379" aria-label="Business card back">
    <defs>
      <linearGradient id="alpineGradient" x1="0" y1="0" x2="0" y2="1">
        <stop offset="0" stop-color="var(--sky-top)"/>
        <stop offset=".55" stop-color="var(--sky-mid)"/>
        <stop offset="1" stop-color="var(--snow)"/>
      </linearGradient>
    </defs>
    <rect class="back-surface" width="620" height="379"/>
    <ellipse class="photo-frame" cx="330" cy="195" rx="265" ry="150" fill="url(#alpineGradient)"
             role="img" aria-label="Photo of a snowboarder jumping above snowy mountain slopes"/>
    <text class="back-brand" x="330" y="200" text-anchor="middle">VARNEX CONSULTING</text>
    <text class="back-services" x="330" y="228" text-anchor="middle">Search &amp; Select | Career | Coaching | Leadership | Outplacement</text>
  </svg>

</main>
</body>
</html>
```